Business Card Design Project

Looking for a logo and business card for a Real State Business i will be opening. The name is not choosen yet , but will probably be RWT IMOVEIS.
I was thinking black and silver colors, but am open to nice ideas.
I did add a business card that i liked a lot, am looking for something like that, with logo in black or silver in a black card. The logo i was thinking in the letters RWT as i uploaded or something or little and cute buildings or a house...just ideas, can be any nice logo.
Updates

You guys can add other colors if you want, I like colors very "BRIGHT" and "open", like red, pink, strong colors. almost glow in the dark colors. lol

Designers,

I've increased more 88 dollars in the budget for 1st place cause I will want envelope designs... small and big sizes.

So 1st place is now U$248,00. 

No need to send the envelope designs right now... only the business cards designs.

Thank you.

Industry/Entity Type

Business

Requirements
Must have
• Marcela Tavares Rocha

www.RWTimoveis-exemplo.com.br

+554187316042

marcela@rwtimoveis-exemplo.com.br

```html
<!DOCTYPE html>
<html lang="pt-BR">
<head>
<meta charset="utf-8">
<title>RWT Imoveis – Cartão de visita</title>
<link href="https://fonts.googleapis.com/css2?family=Didact+Gothic&display=swap" rel="stylesheet">
<style>
  :root {
    --backdrop: #e6e1da;
    --card-black: #050505;
    --silver: #d2d2d2;
    --silver-bright: #f4f4f4;
    --silver-dim: #8c8c8c;
    --text-light: #e9e9e9;
    --shadow: rgba(0, 0, 0, 0.35);
  }
  * { margin: 0; padding: 0; box-sizing: border-box; }
  html, body {
    width: 1200px;
    height: 900px;
    overflow: hidden;
    background: var(--backdrop);
    font-family: "Didact Gothic", "Century Gothic", sans-serif;
  }
  .canvas {
    position: relative;
    width: 1200px;
    height: 900px;
  }
  .card {
    position: absolute;
    width: 600px;
    height: 345px;
    background: var(--card-black);
    box-shadow: 0 6px 18px var(--shadow);
    overflow: hidden;
    color: var(--text-light);
  }
  .card-front { left: 150px; top: 60px; }
  .card-back  { left: 450px; top: 490px; }

  /* front */
  .brand-name {
    position: absolute;
    left: 48px;
    top: 78px;
    font-size: 27px;
    letter-spacing: 1px;
    color: var(--silver);
  }
  .rule {
    position: absolute;
    height: 2px;
    background: linear-gradient(to right, transparent, var(--silver) 40%, var(--silver-bright) 70%, transparent);
  }
  .rule-top    { left: 300px; width: 290px; top: 148px; }
  .rule-mid    { left: 20px;  width: 570px; top: 222px; }
  .rule-bottom { left: 50px;  width: 540px; top: 282px; }
  .silver-band {
    position: absolute;
    left: 0;
    top: 168px;
    width: 600px;
    height: 50px;
    background: linear-gradient(to right, var(--silver-bright) 0%, #ffffff 6%, var(--silver) 20%, var(--silver-dim) 38%, #2a2a2a 52%, var(--card-black) 62%);
  }
  .person {
    position: absolute;
    right: 40px;
    top: 160px;
    text-align: right;
  }
  .person-name { font-size: 18px; letter-spacing: 0.5px; }
  .person-role { font-size: 11px; margin-top: 2px; margin-right: 6px; }
  .contact-row {
    position: absolute;
    left: 50px;
    right: 30px;
    top: 298px;
    display: flex;
    justify-content: space-between;
    font-size: 12.5px;
  }
  .contact-item { display: flex; align-items: center; gap: 6px; white-space: nowrap; }
  .contact-item svg { width: 12px; height: 12px; }

  /* back */
  .back-brand {
    position: absolute;
    left: 50px;
    top: 232px;
    display: flex;
    align-items: center;
    gap: 10px;
    font-size: 20px;
    letter-spacing: 1px;
    color: var(--silver);
  }
  .back-brand .mark {
    width: 14px;
    height: 14px;
    background: var(--silver-dim);
  }
  .back-web {
    position: absolute;
    right: 28px;
    bottom: 22px;
    font-size: 15px;
    letter-spacing: 0.3px;
  }
</style>
</head>
<body>
<main class="canvas">

  <section class="card card-front" aria-label="Frente do cartão">
    <div class="brand-name">RWT IMOVEIS</div>

    <div class="rule rule-top"></div>
    <div class="silver-band"></div>
    <div class="rule rule-mid"></div>

    <div class="person">
      <div class="person-name">Marcela Tavares Rocha</div>
      <div class="person-role">Manager</div>
    </div>

    <div class="rule rule-bottom"></div>

    <div class="contact-row">
      <span class="contact-item">
        <svg viewBox="0 0 12 12" aria-hidden="true"><rect x="3" y="0.5" width="6" height="11" rx="1.2" fill="var(--text-light)"/><rect x="4.2" y="2" width="3.6" height="4.5" fill="var(--card-black)"/></svg>
        554 187 316 042
      </span>
      <span class="contact-item">
        <svg viewBox="0 0 12 12" aria-hidden="true"><rect x="0.8" y="2.5" width="10.4" height="7" fill="none" stroke="var(--text-light)" stroke-width="1.2"/><path d="M1 3 L6 7 L11 3" fill="none" stroke="var(--text-light)" stroke-width="1.2"/></svg>
        marcela@rwtimoveis-exemplo.com.br
      </span>
      <span class="contact-item">
        <svg viewBox="0 0 12 12" aria-hidden="true"><circle cx="6" cy="6" r="5.2" fill="none" stroke="var(--text-light)" stroke-width="1.2"/><ellipse cx="6" cy="6" rx="2.2" ry="5.2" fill="none" stroke="var(--text-light)" stroke-width="1"/><line x1="0.8" y1="6" x2="11.2" y2="6" stroke="var(--text-light)" stroke-width="1"/></svg>
        www.RWTimoveis-exemplo.com.br
      </span>
    </div>
  </section>

  <section class="card card-back" aria-label="Verso do cartão">
    <div class="back-brand"><span class="mark"></span>RWT IMOVEIS</div>
    <div class="back-web">www.RWTimoveis-exemplo.com.br</div>
  </section>

</main>
</body>
</html>
```